Veltrane Group Business Card Design

The CEO is looking for a new trendy look for his business card.
You can stay with current branding or come up with something new/creative. It can be 3D, including Medical Office buildings. You can use our logo in a variety of colors. Please include name, title, company name, company website, email address, cell number

Target Market(s)

Real Estate Development and Construction

Industry/Entity Type

Health care real estate

Contact Information for Business Card

Rohesh Kamdar, CEO M-604.781.2249 E-roheshkamdar@veltrane.com Address:4180 Lindqvist Ave, Tampa, FL 33482 www.veltrane.com

Font styles to use
Other font styles liked:
• Be creative

Requirements
Must have
• Creative, trendy look
Nice to have
• Please go to our website to get a feel- www. veltrane.com
Should not have
• small fonts

```html
<!DOCTYPE html>
<html lang="en">
<head>
<meta charset="utf-8">
<title>Veltrane Group – Business Card</title>
<link href="https://fonts.googleapis.com/css2?family=Montserrat:wght@400;500;700;800&display=swap" rel="stylesheet">
<style>
  :root{
    --navy:#1c3152;
    --navy-soft:#2a4670;
    --red:#b31e2a;
    --white:#ffffff;
    --ink:#2b2b2b;
    --stage:#2e3033;
  }
  *{margin:0;padding:0;box-sizing:border-box}
  html,body{width:1200px;height:874px;overflow:hidden}
  body{
    background:var(--stage);
    font-family:"Montserrat",sans-serif;
    display:flex;flex-direction:column;align-items:center;justify-content:center;gap:24px;
  }
  .card{
    width:700px;height:400px;border-radius:22px;position:relative;overflow:hidden;
  }
  /* back side */
  .card-back{background:var(--navy);}
  .card-back .brand-mark{
    position:absolute;left:70px;top:90px;
    font-weight:800;color:var(--navy-soft);line-height:.95;
  }
  .card-back .brand-mark .word{display:block;font-size:118px;letter-spacing:-4px}
  .card-back .brand-mark .sub{display:block;font-size:64px;text-align:right;letter-spacing:-1px}
  /* front side */
  .card-front{background:var(--white);}
  .card-front svg.swoosh{position:absolute;inset:0}
  .contact{
    position:absolute;left:30px;top:200px;list-style:none;color:var(--white);
    font-size:15px;font-weight:500;line-height:1.3;
  }
  .contact li{display:flex;align-items:flex-start;gap:9px;margin-bottom:9px}
  .contact svg{flex:none;margin-top:2px}
  .brand{
    position:absolute;right:46px;top:70px;text-align:right;
    color:var(--red);font-weight:800;line-height:.95;
  }
  .brand .word{display:block;font-size:60px;letter-spacing:-2px}
  .brand .sub{display:block;font-size:34px}
  .person{position:absolute;right:46px;bottom:56px;text-align:right}
  .person .name{color:var(--red);font-weight:700;font-size:28px;letter-spacing:1px}
  .person .title{color:var(--ink);font-size:20px;font-weight:400;margin-top:4px}
  .accent-bar{position:absolute;right:0;bottom:56px;width:22px;height:66px;background:var(--red)}
</style>
</head>
<body>

  <section class="card card-back" aria-label="Card back">
    <div class="brand-mark"><span class="word">Veltrane</span><span class="sub">Group</span></div>
  </section>

  <section class="card card-front" aria-label="Card front">
    <svg class="swoosh" viewBox="0 0 700 400" width="700" height="400" aria-hidden="true">
      <path fill="var(--red)" d="M14 0 C20 110 230 120 320 260 C360 320 340 370 330 400 H364 C374 372 397 318 354 250 C262 110 48 100 40 0 Z"/>
      <path fill="var(--navy)" stroke="var(--white)" stroke-width="4" d="M-2 -2 H14 C20 110 230 120 320 260 C360 320 340 370 330 402 H-2 Z"/>
    </svg>

    <ul class="contact">
      <li>
        <svg width="14" height="18" viewBox="0 0 14 18"><path fill="var(--red)" d="M7 0a7 7 0 0 0-7 7c0 5 7 11 7 11s7-6 7-11a7 7 0 0 0-7-7zm0 9.5A2.5 2.5 0 1 1 7 4.5a2.5 2.5 0 0 1 0 5z"/></svg>
        <span>4180 Lindqvist Ave,<br>Tampa, FL 33482</span>
      </li>
      <li>
        <svg width="14" height="18" viewBox="0 0 14 18"><rect x="1.5" y="1" width="11" height="16" rx="2" fill="none" stroke="var(--red)" stroke-width="2"/><circle cx="7" cy="14" r="1.2" fill="var(--red)"/></svg>
        <span>604.781.2249</span>
      </li>
      <li>
        <svg width="16" height="14" viewBox="0 0 16 14"><rect x="1" y="2" width="14" height="10" fill="var(--red)"/><path d="M1 2 L8 8 L15 2" fill="none" stroke="var(--navy)" stroke-width="1.5"/></svg>
        <span>roheshkamdar@veltrane.com</span>
      </li>
      <li>
        <svg width="16" height="16" viewBox="0 0 16 16"><circle cx="8" cy="8" r="7" fill="none" stroke="var(--red)" stroke-width="2"/><path d="M1 8h14M8 1c3 3 3 11 0 14M8 1c-3 3-3 11 0 14" fill="none" stroke="var(--red)" stroke-width="1.3"/></svg>
        <span>www.veltrane.com</span>
      </li>
    </ul>

    <div class="brand"><span class="word">Veltrane</span><span class="sub">Group</span></div>

    <div class="person">
      <div class="name">ROHESH KAMDAR</div>
      <div class="title">CEO</div>
    </div>
    <div class="accent-bar"></div>
  </section>

</body>
</html>
```